Business card design for Corvane Engineering Tandem

We need a new business card design along with all the necessary to place an order. The company is Corvane Engineering Tandem and we recently updated our logo.

```html
<!DOCTYPE html>
<html lang="en">
<head>
<meta charset="utf-8">
<title>Corvane Engineering Tandem – Business Card</title>
<link href="https://fonts.googleapis.com/css2?family=Roboto:wght@400;500;700&display=swap" rel="stylesheet">
<style>
  :root {
    --bg-dark: #2b2b2b;
    --bg-light: #4a4a4a;
    --card-white: #fdfdfd;
    --card-black: #161616;
    --ink-grey: #8f8f8f;
    --ink-light: #bdbdbd;
    --accent-yellow: #e3bb1f;
  }
  * { margin: 0; padding: 0; box-sizing: border-box; }
  html, body {
    width: 1200px; height: 694px; overflow: hidden;
  }
  body {
    background: linear-gradient(135deg, var(--bg-dark) 0%, var(--bg-light) 100%);
    font-family: "Roboto", Arial, sans-serif;
    position: relative;
  }
  .card {
    position: absolute;
    top: 197px;
    width: 510px;
    height: 300px;
    border-radius: 26px;
    box-shadow: 0 18px 40px rgba(0,0,0,0.45);
  }
  .card--front {
    left: 60px;
    background: var(--card-white);
    display: flex;
    align-items: center;
    justify-content: center;
    gap: 14px;
  }
  .brand-mark {
    width: 22px; height: 22px;
    flex: none;
    background: var(--accent-yellow);
  }
  .brand-name {
    font-weight: 500;
    font-size: 30px;
    color: var(--ink-grey);
    letter-spacing: 0.5px;
    white-space: nowrap;
  }
  .card--back {
    left: 630px;
    background: var(--card-black);
    color: var(--ink-light);
  }
  .contact-top {
    position: absolute;
    top: 40px; left: 36px; right: 36px;
    height: 112px;
    display: flex;
  }
  .contact-left { flex: 1; }
  .divider-vertical {
    width: 1px; height: 62px;
    background: var(--accent-yellow);
    margin: 4px 26px 0;
  }
  .contact-right { flex: 1; padding-top: 8px; }
  .person-name {
    font-weight: 700;
    font-size: 24px;
    color: var(--ink-grey);
  }
  .person-role {
    font-size: 10px;
    letter-spacing: 4px;
    color: var(--accent-yellow);
    margin-top: 4px;
    margin-left: 60px;
  }
  .field-label {
    display: flex; align-items: center; gap: 6px;
    font-size: 10px;
    letter-spacing: 4px;
    color: var(--accent-yellow);
    text-transform: uppercase;
  }
  .field-label svg { width: 13px; height: 13px; fill: var(--accent-yellow); }
  .field-value {
    font-size: 13.5px;
    color: var(--ink-light);
    margin-top: 3px;
    white-space: nowrap;
  }
  .email-block { margin-top: 22px; }
  .rule {
    position: absolute;
    left: 20px; right: 20px;
    height: 1px;
    background: var(--accent-yellow);
  }
  .rule--upper { top: 168px; }
  .rule--lower { top: 272px; }
  .phone-block {
    position: absolute;
    top: 180px; left: 40px;
  }
  .phone-number {
    font-weight: 700;
    font-size: 58px;
    line-height: 1;
    color: var(--ink-grey);
    -webkit-text-stroke: 1px var(--accent-yellow);
    letter-spacing: 1px;
    margin-top: 4px;
    white-space: nowrap;
  }
</style>
</head>
<body>
  <div class="card card--front">
    <span class="brand-mark"></span>
    <span class="brand-name">Corvane Engineering Tandem</span>
  </div>

  <div class="card card--back">
    <div class="contact-top">
      <div class="contact-left">
        <div class="person-name">Helen Marsh</div>
        <div class="person-role">DIRECTOR</div>
        <div class="email-block">
          <div class="field-label">
            <svg viewBox="0 0 16 16"><path d="M1 3h14v10H1z M1 3l7 6 7-6" fill="none" stroke="#e3bb1f" stroke-width="1.6"/></svg>
            E-mail
          </div>
          <div class="field-value">sales@corvaneengineering.co.uk</div>
        </div>
      </div>
      <div class="divider-vertical"></div>
      <div class="contact-right">
        <div class="field-label">
          <svg viewBox="0 0 16 16"><circle cx="8" cy="8" r="6.5" fill="none" stroke="#e3bb1f" stroke-width="1.5"/><path d="M1.5 8h13M8 1.5c-3 3-3 10 0 13M8 1.5c3 3 3 10 0 13" fill="none" stroke="#e3bb1f" stroke-width="1.2"/></svg>
          Web
        </div>
        <div class="field-value">www.corvaneengineering.co.uk</div>
      </div>
    </div>

    <div class="rule rule--upper"></div>

    <div class="phone-block">
      <div class="field-label">
        <svg viewBox="0 0 16 16"><path d="M4 1.5l2.5 3-1.5 1.8c.8 1.8 2.2 3.2 4 4l1.8-1.5 3 2.5-1.5 2.7C7.5 13.8 2.2 8.5 1.3 3z"/></svg>
        Phone
      </div>
      <div class="phone-number">01632 960418</div>
    </div>

    <div class="rule rule--lower"></div>
  </div>
</body>
</html>
```